Website Redesign for Non-Profit Ministry & Church

NOTE: Please do not contact me privately — all private inquiries will be ignored.

Individuals seeking spiritual healing, community connection, ministry support and journal-based encounters.

Description of What’s Needed

We need a clean, fresh, inviting website that encourages engagement and connection. The site should feel warm and accessible, draw people in, and clearly present who we are, what we offer, and how visitors can participate. The layout should be straightforward, with well-structured pages (no overlapping objects, minimal layering complexity) and easy to navigate. Use only Google Fonts. All stock photos must be sourced from royalty-free sites and include proper attribution. We will not include a search feature.

Pages to Create
1. Home Page – impactful hero area, clear call-to-action, visual story of ministry, giving/gathering invitation.
2. About Us – vision, mission, leadership, testimonies, history.
3. Meetings & Events – upcoming gatherings, schedule, how to attend, sign-up or interest form.
4. Encounter: “Lanterns by the River” (book) – dedicated page for the book, overview, purchase link or details, journal prompts, imagery.
5. Healing Rooms / Ministry – explain ministry offerings, invite participation, testimonials or case-studies.
6. Live Stream & Links Page – page listing links for YouTube live stream, other platforms, archive links; simple layout.

Colour & Branding

Use colours that blend with our existing logo (attached). The palette should feel contemporary, welcoming, and aligned with ministry themes of restoration, healing and love. Ensure text, button and link colours maintain good contrast for accessibility.

Existing Content & Reference

Please gather available content from our current website in the attachment here for text, images and structure for reuse.

Imagery Guidelines

– Use original photos from our Facebook page or Google Location listing for building or people images when available.
– If generic images are used, ensure they depict appropriate ministry-related buildings or people (community, warm gathering) — avoid generic unrelated stock imagery.
– All photos must be royalty-free or have proper licensing and attribution.
– No overlapping objects or visual clutter; clean layouts with defined sections.

Additional Notes

– Integration: We currently utilise MailChimp for email communication; the design should include a connection/invite to subscribe (via MailChimp) but no blog page is required at this time.
– Payment/Giving: We accept PayPal and already have a giving portal; include clear donation/give buttons or calls-to-action linking to existing giving systems.
– No search function to be included.
– Layouts should avoid complex layering or overlapping elements—designers should work with distinct content blocks, clear visual hierarchy, and straightforward mobile-friendly structure.

Target Market(s)

Industry/Entity Type

Church/Religious institution

Number of Pages Required

5+ page

Requirements
Should not have
• search bar

```html
<!DOCTYPE html>
<html lang="en">
<head>
<meta charset="utf-8">
<title>Restored &amp; Renewed – Home</title>
<link href="https://fonts.googleapis.com/css2?family=Fredoka:wght@500;600&family=Roboto:wght@400;500;700&display=swap" rel="stylesheet">
<style>
:root{
  --teal:#00a393;
  --teal-soft:#bfe6e0;
  --purple:#5b2a86;
  --green:#0d6b3a;
  --text:#555b5e;
  --ink:#222;
  --white:#fff;
}
*{box-sizing:border-box;margin:0;padding:0}
html,body{width:1200px;height:3173px;overflow:hidden}
body{position:relative;font-family:'Roboto',sans-serif;color:var(--text);background:var(--white)}
.abs{position:absolute}
.display{font-family:'Fredoka',sans-serif;font-weight:600;letter-spacing:-1px}
.btn{position:absolute;display:flex;align-items:center;justify-content:center;border-radius:30px;color:var(--white);font-weight:700;font-size:16px;text-transform:uppercase;text-decoration:none}
.btn-purple{background:var(--purple)}
.btn-teal{background:var(--teal)}

/* top bar & nav */
.top-line{top:0;left:0;width:1200px;height:4px;background:var(--teal);z-index:5}
.brand{left:145px;top:40px;display:flex;align-items:center;gap:12px;z-index:5}
.brand-dot{width:54px;height:54px;border-radius:50%;background:var(--teal)}
.brand-name{font-weight:700;font-size:26px;line-height:1.05;color:var(--green);width:150px}
.nav{left:432px;top:0;display:flex;gap:23px;z-index:5;font-size:15px;font-weight:500;color:var(--ink)}
.nav a{display:block;padding-top:66px;color:inherit;text-decoration:none}
.nav a.active{background:var(--teal);color:var(--white);padding:66px 14px 40px;border-radius:0 0 34px 34px}

/* hero */
.hero-photo{top:0;left:0;width:1200px;height:900px;
  background:
    radial-gradient(ellipse 420px 300px at 720px 330px,rgba(120,170,210,.55),rgba(120,170,210,0)),
    radial-gradient(ellipse 360px 180px at 900px 560px,rgba(238,200,175,.75),rgba(238,200,175,0)),
    radial-gradient(ellipse 600px 250px at 300px 720px,rgba(120,150,70,.6),rgba(120,150,70,0)),
    linear-gradient(180deg,#dbe6f6 0%,#e9eef2 30%,#d6e3c8 55%,#a9c486 78%,#86a463 100%)}
.hero-fade{top:0;left:0;width:1200px;height:900px}
.hero-circle{left:140px;top:243px;width:425px;height:425px;border-radius:50%;background:var(--white);border:5px solid var(--teal);text-align:center;padding-top:100px}
.hero-title{font-size:44px;line-height:1.1;color:var(--green)}
.hero-title .p{color:var(--purple)}
.hero-title .t{color:var(--teal)}
.hero-sub{margin-top:18px;font-size:20px;line-height:30px;color:var(--ink)}
.dots{left:1128px;top:397px;display:flex;flex-direction:column;gap:13px}
.dots span{width:10px;height:10px;border-radius:50%;background:#c9c9c9}
.dots span:first-child{background:var(--purple)}

/* story */
.story-bg{top:1180px;left:0;width:1200px;height:440px;background:linear-gradient(180deg,rgba(255,255,255,0),#dde2e5 55%,#e8efec 100%)}
.blob{border-radius:48% 52% 45% 55%/55% 45% 55% 45%;border-left:10px solid var(--teal)}
.story-photo{left:123px;top:990px;width:427px;height:425px;background:linear-gradient(135deg,#cfc2b1,#7a6a98 60%,#2f3a5a)}
.section-title{font-size:58px;line-height:1}
.story-title{left:615px;top:985px;color:var(--green)}
.story-title span{color:var(--purple)}
.story-text{left:615px;top:1075px;width:437px;font-size:15px;line-height:31px;text-align:justify}

/* invite */
.invite-bg{top:1620px;left:0;width:1200px;height:760px;background:linear-gradient(135deg,#e3efeb 0%,#eef3f0 50%,#e7e4f0 100%)}
.invite-title{left:145px;top:1768px;color:var(--green)}
.invite-text{left:145px;top:1855px;width:438px;font-size:15px;line-height:31px;text-align:justify}
.invite-text b{color:var(--ink);font-weight:500}
.invite-photo{left:628px;top:1815px;width:427px;height:425px;background:linear-gradient(160deg,#3d3a33,#8a4a2e 55%,#b9a7c9)}

/* newsletter */
.newsletter{left:144px;top:2316px;width:912px;height:438px;border-radius:140px;background:var(--teal);text-align:center;color:var(--white)}
.newsletter h2{margin-top:55px;font-size:58px}
.newsletter .lead{margin-top:14px;font-size:18px}
.fields{display:flex;gap:14px;justify-content:center;margin-top:32px}
.field{width:225px;height:52px;background:var(--white);border-radius:3px;color:#555;font-size:14px;display:flex;align-items:center;padding-left:28px}
.newsletter .btn{left:366px;top:282px;width:180px;height:58px}
.newsletter .note{position:absolute;left:0;width:912px;top:365px;font-size:11px}

/* footer */
.foot-col{top:2842px}
.foot-col h3{font-size:22px;font-weight:500;color:var(--teal);margin-bottom:22px}
.foot-col li{list-style:none;font-size:15px;line-height:33px;color:var(--text)}
.divider{top:2838px;width:1px;height:237px;background:#ddd}
.social{display:flex;gap:12px}
.social span{width:38px;height:38px;border-radius:50%;border:2px solid var(--ink)}
.social span:first-child{border-color:var(--purple)}
.bottom-bar{left:0;top:3125px;width:1200px;height:48px;background:var(--purple);color:var(--white);font-size:15px;display:flex;align-items:center;justify-content:center}
</style>
</head>
<body>

<div class="abs hero-photo" role="img" aria-label="Butterfly above open hands in a sunlit meadow of tall grass"></div>
<svg class="abs hero-fade" width="1200" height="900" viewBox="0 0 1200 900" aria-hidden="true">
  <path d="M0 780 C300 860 600 860 900 740 C1020 690 1120 680 1200 700 L1200 900 L0 900 Z" fill="#fff"/>
</svg>
<div class="abs top-line"></div>

<div class="abs brand"><span class="brand-dot"></span><span class="brand-name">Restored &amp; Renewed</span></div>

<nav class="abs nav">
  <a class="active" href="#">Home</a>
  <a href="#">About Us</a>
  <a href="#">Meetings &amp; Events</a>
  <a href="#">Encounter</a>
  <a href="#">Healing Rooms</a>
  <a href="#">Live Stream</a>
</nav>

<div class="abs dots"><span></span><span></span><span></span></div>

<div class="abs hero-circle">
  <h1 class="display hero-title">Restored, <span class="p">Loved,</span><br><span class="t">Renewed</span></h1>
  <p class="hero-sub">Loving the broken. Leading<br>them home.</p>
</div>
<a class="btn btn-purple" style="left:267px;top:544px;width:180px;height:59px">Get Started</a>

<div class="abs story-bg" role="img" aria-label="Faded view of the ministry building among winter trees"></div>
<div class="abs blob story-photo" role="img" aria-label="Photo of the ministry couple in front of a stained glass window"></div>
<h2 class="abs display section-title story-title">Our <span>Story</span></h2>
<p class="abs story-text">Daniel and Ann Louise have been married for 42 years and have two adult children. They both grew up in central Ohio. Their desire is to share the love of Christ with others. They have numerous stories to share about the many ways they have seen God move in their lives as well as the lives of others. They believe in the manifestation of God’s power through signs and wonders. They have not only witnessed God’s power through signs and wonders them they have also experienced His miraculous healing touch personally.</p>
<a class="btn btn-purple" style="left:615px;top:1385px;width:180px;height:58px">Read More</a>
<a class="btn btn-teal" style="left:801px;top:1385px;width:204px;height:58px">Vision &amp; Mission</a>

<div class="abs invite-bg" role="img" aria-label="Soft misty backdrop of fern leaves"></div>

<h2 class="abs display section-title invite-title">Invite</h2>
<p class="abs invite-text"><b>If you are hosting an event at your church or ministry, as you prayerfully seek the Lord for guidance review these thoughts regarding Ann Louise &amp; Daniel Hollander and their ministry.</b><br>I have served in church leadership with Ann Louise and Daniel for several years, and I do not know of a more balanced and powerful ministry of miracles and healings. They are activators not only of supernatural demonstrations but of supernatural compassion.</p>
<a class="btn btn-purple" style="left:145px;top:2133px;width:181px;height:58px">Read More</a>
<div class="abs blob invite-photo" role="img" aria-label="Ministry team waving before a large gathered crowd"></div>

<section class="abs newsletter">
  <h2 class="display">Join Our Newsletter</h2>
  <p class="lead">Signup today for free and be the first to get notified on new updates.</p>
  <div class="fields">
    <div class="field">Enter Your Email</div>
    <div class="field">Enter First Name</div>
    <div class="field">Enter Last Name</div>
  </div>
  <a class="btn btn-purple">Subscribe</a>
  <p class="note">And don't worry, we hate spam too! You can unsubscribe at anytime.</p>
</section>

<div class="abs foot-col" style="left:148px">
  <h3>RECENT POSTS</h3>
  <ul>
    <li>Nothing is incurable for God</li>
    <li>Healing amidst the car accident</li>
    <li>Healing – where and how can it happen?</li>
    <li>Why is healing important?</li>
    <li>Now is the time to move!</li>
  </ul>
</div>
<div class="abs divider" style="left:466px"></div>
<div class="abs foot-col" style="left:510px">
  <h3>LINKS</h3>
  <div style="display:flex;gap:34px">
    <ul><li>Home</li><li>About Us</li><li>Meetings &amp; Events</li></ul>
    <ul><li>Encounter</li><li>Healing Rooms</li><li>Live Stream</li></ul>
  </div>
</div>
<div class="abs divider" style="left:826px"></div>
<div class="abs foot-col" style="left:896px">
  <h3>SOCIAL MEDIA</h3>
  <div class="social"><span aria-label="Social profile one"></span><span aria-label="Social profile two"></span></div>
</div>

<footer class="abs bottom-bar">Copyright © 2025 Companyname. All Rights Reserved. | Powered by brightpage.studio</footer>

</body>
</html>
```